BrimLO (Beer/Wine candles) Edgy Candle with a Cause

Help us to help others. BrimLo is a beautifully scented natural soy candle made using repurposed beer/ wine bottles while at the same time donating a portion of our profits to youth alcohol education programs. (1. Waste = Repurposed beer/wine bottle, 2.) BrimLo = (anti) drunk/alcohol 3.) Ed = education/prevention programs.)
We're looking for a design that is cool and bold yet elegant and appeals to women (90% of our customers.) No traditional beer label designs please.

The "BrimLO" logo should appear prominently in the design with the scent name (in a different font) "on top." (See the "Velvet Brimmed" poster attached.

Examples of actual scents: Amber Drift, Glowing Paloma, Fizzing Mock-ree. (None of the fragrances smell like beer/alcohol or wine.)

Also the ED in BrimeLO should stand out in some way.

The emphasis should not be on the recycling aspect, so no obvious recycling symbols.

We are open to different interpretations and have attached varying examples that we like.
Note: a "blackboard/chalkboard" label is an idea since this deals with education.

Note: files & fonts used in the final design should be editable so that we can add other scent names as needed.

Target Market(s)

Candle buyers, specifically women between the ages of 16-45

Requirements
Must have
• 1.)Free fonts or license fonts under $20.00 2.) fonts modified to look unique/original. 3.) Editable Scent name 4.) Burning instructions 5.) Warning Info
• Burning Instructions: Trim wick to 1/4" before each lighting. Keep free from foreign materials including wick trimmings. For an even burn, burn for at least 1 hour but not more than 4 hours at a time. Discontinue use when 1/4" of wax remains. Discard or recycle after use.
• Warning: Burn candle within sight. Keep out of reach of children and pets. Keep away from things that catch fire. Use with caution.
Nice to have
• Colored Scent Names
Should not have
• recycle symbols

```html
<!DOCTYPE html>
<html lang="en">
<head>
<meta charset="utf-8">
<title>BrimLo Amber Drift Label</title>
<link rel="stylesheet" href="https://fonts.googleapis.com/css2?family=Architects+Daughter&family=Cabin+Sketch:wght@700&family=Gochi+Hand&display=swap">
<style>
  :root {
    --page: #e6e6e6;
    --board: #2a2a2a;
    --board-dark: #1c1c1c;
    --board-light: #3a3a3a;
    --chalk: #ecebe4;
    --chalk-soft: #cfcdc4;
    --amber: #f0b429;
    --coral: #ef6a4c;
  }
  * { margin: 0; padding: 0; box-sizing: border-box; }
  html, body { width: 1200px; height: 1200px; overflow: hidden; }
  body { background: var(--page); position: relative; font-family: "Architects Daughter", cursive; color: var(--chalk); }

  .label {
    position: absolute; left: 40px; top: 178px; width: 1120px; height: 845px;
    background:
      radial-gradient(ellipse at 30% 25%, var(--board-light) 0%, transparent 55%),
      radial-gradient(ellipse at 75% 80%, #333 0%, transparent 50%),
      linear-gradient(160deg, var(--board) 0%, var(--board-dark) 100%);
    box-shadow: 0 2px 6px rgba(0,0,0,.25);
  }
  .label > * { position: absolute; }

  .tagline { left: 45px; top: 26px; width: 190px; font-size: 29px; line-height: 1.12; }
  .tagline-arrow { left: 248px; top: 70px; width: 40px; height: 240px; }

  .scent-name { left: 335px; top: 88px; font-family: "Gochi Hand", cursive; font-size: 66px; color: var(--amber); line-height: 1; white-space: nowrap; }
  .scent-rule { left: 312px; top: 168px; width: 430px; height: 14px; }

  .brand { left: 262px; top: 215px; display: flex; align-items: flex-end; gap: 12px; }
  .brand-name { font-family: "Architects Daughter", cursive; font-weight: 400; font-size: 136px; line-height: 1.2; color: var(--coral); white-space: nowrap; }
  .brand-dot { width: 22px; height: 22px; border: 3px solid var(--chalk); border-radius: 50%; margin-bottom: 40px; }

  .product-line { left: 300px; top: 505px; width: 420px; text-align: center; font-family: "Cabin Sketch", cursive; font-weight: 700; font-size: 36px; color: var(--chalk); }

  .origin { left: 235px; top: 595px; width: 440px; height: 58px; border: 3px solid var(--chalk-soft); border-radius: 6px; font-size: 32px; text-align: center; line-height: 52px; }

  .maker-mark { left: 490px; top: 700px; width: 44px; height: 40px; background: var(--amber); border-radius: 4px; opacity: .85; }

  .net-weight { left: 310px; top: 760px; width: 400px; text-align: center; font-size: 38px; }

  .burn-box { left: 20px; top: 330px; width: 190px; height: 490px; border: 3px solid var(--amber); border-radius: 10px 10px 40px 10px; overflow: hidden; }
  .burn-text {
    position: absolute; left: 50%; top: 50%; width: 450px;
    transform: translate(-50%, -50%) rotate(-90deg);
    font-size: 17px; line-height: 1.3; color: var(--chalk);
  }
  .burn-text strong { color: var(--amber); font-weight: 400; }

  .ingredients { left: 790px; top: 28px; width: 320px; }
  .ingredients-title { font-size: 30px; padding-left: 30px; margin-bottom: 4px; }
  .ingredient-list { list-style: none; font-size: 29px; line-height: 1.25; }
  .ingredient-list li { display: flex; align-items: center; gap: 6px; }
  .tick { width: 24px; height: 24px; flex: none; }

  .cause { left: 800px; top: 340px; width: 300px; font-size: 27px; line-height: 1.2; }
  .cause .marked { text-decoration: underline; text-decoration-thickness: 2px; text-underline-offset: 6px; }

  .quality { left: 740px; top: 570px; width: 360px; height: 190px; border: 3px solid var(--chalk-soft); border-radius: 50%; display: flex; align-items: center; justify-content: center; text-align: center; padding: 0 48px; font-size: 22px; line-height: 1.2; }
</style>
</head>
<body>
  <section class="label">
    <p class="tagline">PASSionately saving futures drowning with alcohol</p>
    <svg class="tagline-arrow" viewBox="0 0 40 240" aria-hidden="true">
      <path d="M20 236 L20 8 M6 30 L20 6 L34 30" fill="none" stroke="#ecebe4" stroke-width="5" stroke-linecap="round" stroke-linejoin="round"/>
    </svg>

    <h2 class="scent-name">Amber Drift</h2>
    <svg class="scent-rule" viewBox="0 0 430 14" aria-hidden="true">
      <path d="M4 9 Q215 3 426 7" fill="none" stroke="#f0b429" stroke-width="4" stroke-linecap="round"/>
    </svg>

    <div class="brand">
      <h1 class="brand-name">BrimLo</h1>
      <span class="brand-dot"></span>
    </div>
    <p class="product-line">Beer Bottle Candles</p>

    <p class="origin">Handmade in USA</p>
    <div class="maker-mark" role="img" aria-label="Small maker mark"></div>
    <p class="net-weight">11oz · 311g.</p>

    <div class="burn-box">
      <p class="burn-text"><strong>Burning Instructions:</strong> Trim wick to 1/4" before each lighting. Keep free of foreign materials. Burn at least 1 hour, no more than 4 hours. <strong>Warning:</strong> Burn within sight. Keep from children and pets.</p>
    </div>

    <div class="ingredients">
      <p class="ingredients-title">ingredients:</p>
      <ul class="ingredient-list">
        <li><svg class="tick" viewBox="0 0 26 26" aria-hidden="true"><path d="M3 14 L10 22 L23 4" fill="none" stroke="#ecebe4" stroke-width="3" stroke-linecap="round" stroke-linejoin="round"/></svg>natural soy wax</li>
        <li><svg class="tick" viewBox="0 0 26 26" aria-hidden="true"><path d="M3 14 L10 22 L23 4" fill="none" stroke="#ecebe4" stroke-width="3" stroke-linecap="round" stroke-linejoin="round"/></svg>100% cotton wick</li>
        <li><svg class="tick" viewBox="0 0 26 26" aria-hidden="true"><path d="M3 14 L10 22 L23 4" fill="none" stroke="#ecebe4" stroke-width="3" stroke-linecap="round" stroke-linejoin="round"/></svg>natural fragrance</li>
        <li><svg class="tick" viewBox="0 0 26 26" aria-hidden="true"><path d="M3 14 L10 22 L23 4" fill="none" stroke="#ecebe4" stroke-width="3" stroke-linecap="round" stroke-linejoin="round"/></svg>passion</li>
        <li><svg class="tick" viewBox="0 0 26 26" aria-hidden="true"><path d="M3 14 L10 22 L23 4" fill="none" stroke="#ecebe4" stroke-width="3" stroke-linecap="round" stroke-linejoin="round"/></svg>advocacy</li>
      </ul>
    </div>

    <p class="cause">Portion of the sales go to support <span class="marked">underage drinking</span> prevention programs.</p>

    <p class="quality">high quality soy candles handcrafted from the finest ingredients in repurposed/recycled beer bottles.</p>
  </section>
</body>
</html>
```